Business card for my new company (Accounting firm)

I need a business card for my new business Brightwell Advisory and Ledger SA. Our services are accounting, tax, audit and financial management. Our customers are small companies, start-ups and new companies. The final design has to show financial security, trust and growth. Please find our logo attached to the business card. Text for the business card: Brightwell Advisory and Ledger SA Tomas Varenholt Director and Founder Certified Accountant Tel. 022 418 57 34 tv@clairevalconseil.ch www.clairevalconseil.ch Rue des Vergières 27 1201 Geneva
Target Market(s)
Our customers are small companies, start-ups and new companies.
Industry/Entity Type
Finance And Accounting
Contact Information for Business Card
Claireval Conseil et Comptes SA
Tomas Varenholt
Directeur et Fondateur
Expert-comptable diplômé
Tél. 022 418 57 34
tv@clairevalconseil.ch
www.clairevalconseil.ch
Rue des Vergières 27
1201 Genève

```html
<!DOCTYPE html>
<html lang="fr">
<head>
<meta charset="utf-8">
<title>Claireval Conseil et Comptes SA – Carte de visite</title>
<link href="https://fonts.googleapis.com/css2?family=Montserrat:wght@500&family=Roboto:wght@400;500;700&display=swap" rel="stylesheet">
<style>
  :root{
    --bg:#e4e5e7;
    --card-white:#ffffff;
    --card-grey-top:#f4f4f5;
    --card-grey-bottom:#e9eaeb;
    --blue-light:#2ea3da;
    --blue-mid:#1c82c2;
    --blue-dark:#14588f;
    --ink:#3b3b3d;
    --ink-soft:#555759;
    --rule:#3d3f42;
  }
  *{box-sizing:border-box;margin:0;padding:0}
  html,body{width:1200px;height:726px;overflow:hidden}
  body{background:var(--bg);font-family:"Roboto",Arial,sans-serif;position:relative}

  .card{
    position:absolute;top:208px;width:540px;height:310px;
    border-radius:3px;overflow:hidden;
    box-shadow:0 2px 6px rgba(0,0,0,.12);
  }
  .card--front{left:40px;background:var(--card-white)}
  .card--back{left:620px;background:linear-gradient(180deg,var(--card-grey-top),var(--card-grey-bottom))}

  .brand{
    position:absolute;display:flex;align-items:center;gap:14px;
    font-family:"Montserrat",Arial,sans-serif;font-weight:500;color:var(--ink);
    text-transform:uppercase;letter-spacing:.12em;line-height:1.25;font-size:19px;
    white-space:nowrap;
  }
  .brand__mark{width:30px;height:30px;background:var(--blue-mid);flex:none}
  .card--front .brand{left:150px;top:98px}
  .card--back .brand{left:32px;top:146px;font-size:14px;letter-spacing:.08em;gap:12px}
  .card--back .brand__mark{width:26px;height:26px}

  .front-stripe{
    position:absolute;left:0;right:0;top:246px;height:9px;
    background:linear-gradient(90deg,var(--blue-dark),var(--blue-light));
  }

  .contact{position:absolute;left:322px;top:48px;color:var(--ink-soft);white-space:nowrap}
  .contact__name{font-weight:700;font-size:20px;color:var(--blue-dark);margin-bottom:6px}
  .contact__role{font-size:12.5px;line-height:1.3}
  .contact__list{list-style:none;margin-top:16px;font-size:13px}
  .contact__list li{display:flex;align-items:center;gap:10px;height:20px}
  .contact__list svg{width:12px;height:12px;fill:var(--blue-dark);flex:none}

  .back-rule{position:absolute;left:0;right:0;top:262px;height:3px;background:var(--rule)}
  .back-band{
    position:absolute;left:0;right:0;top:265px;bottom:0;
    background:linear-gradient(90deg,var(--blue-dark),var(--blue-light));
    color:#fff;font-size:14px;display:flex;align-items:center;justify-content:flex-end;padding-right:36px;
  }
</style>
</head>
<body>
  <section class="card card--front" aria-label="Recto">
    <div class="brand"><span class="brand__mark"></span><span>Claireval<br>Conseil et Comptes</span></div>
    <div class="front-stripe"></div>
  </section>

  <section class="card card--back" aria-label="Verso">
    <div class="brand"><span class="brand__mark"></span><span>Claireval<br>Conseil et Comptes</span></div>
    <div class="contact">
      <p class="contact__name">Tomas Varenholt</p>
      <p class="contact__role">Directeur et Fondateur<br>Expert-comptable diplômé</p>
      <ul class="contact__list">
        <li><svg viewBox="0 0 12 12" aria-hidden="true"><path d="M2.4 0.8l2 2-1 1.3c.6 1.5 1.9 2.8 3.4 3.4l1.3-1 2 2-1.2 1.8C4.7 10.2 1.8 7.3 0.6 2z"/></svg>022 418 57 34</li>
        <li><svg viewBox="0 0 12 12" aria-hidden="true"><path d="M0 2h12v8H0z M1 3v.3l5 3.4 5-3.4V3z" fill-rule="evenodd"/></svg>tv@clairevalconseil.ch</li>
        <li><svg viewBox="0 0 12 12" aria-hidden="true"><path d="M6 0a6 6 0 100 12A6 6 0 006 0zm-.6 1.2v2.3H3.6c.4-1.2 1-2 1.8-2.3zm1.2 0c.8.3 1.4 1.1 1.8 2.3H6.6zM1.6 4.7h1.7v2.6H1.6zm3.8 0v2.6H4.5V4.7zm1.2 0h.9v2.6h-.9zm2.1 0h1.7v2.6H8.7zM3.6 8.5h1.8v2.3c-.8-.3-1.4-1.1-1.8-2.3zm3 0h1.8c-.4 1.2-1 2-1.8 2.3z"/></svg>www.clairevalconseil.ch</li>
      </ul>
    </div>
    <div class="back-rule"></div>
    <div class="back-band">Rue des Vergières 27 1201 Genève</div>
  </section>
</body>
</html>
```